Whitcombe Business Card Design

The name of the business is Dario Whitcombe, CPA LLC
The service that we offer is Accounting, Tax & Consulting Services. I need it to have the following items:
Dario Whitcombe, Principal
Phone Number
Email Address
Physical Address

I have attached the company logo, one in black and one in white. Please provide a design in black background and the other in white background. Please include "Accounting, Tax & Consulting Services". I want the business card to be clean and very professional.

```html
<!DOCTYPE html>
<html lang="en">
<head>
<meta charset="utf-8">
<title>Dario Whitcombe, CPA LLC — Business Card</title>
<link rel="stylesheet" href="https://fonts.googleapis.com/css2?family=Montserrat:wght@400;500;600;700&display=swap">
<style>
  :root {
    --stage: #121212;
    --card: #1f1f20;
    --red: #a3232a;
    --grey: #6a6a6c;
    --light: #ececec;
  }
  * { box-sizing: border-box; margin: 0; padding: 0; }
  html, body { width: 1200px; height: 900px; overflow: hidden; }
  body {
    background: var(--stage);
    font-family: "Montserrat", Arial, sans-serif;
    display: flex;
    flex-direction: column;
    align-items: center;
    justify-content: center;
    gap: 40px;
  }
  .card {
    width: 700px;
    height: 400px;
    background: var(--card);
    border-radius: 18px;
    position: relative;
    box-shadow: 0 10px 30px rgba(0,0,0,.6);
  }
  .lockup {
    display: flex;
    align-items: center;
    gap: 18px;
  }
  .lockup__square {
    width: 46px;
    height: 46px;
    background: var(--red);
    flex: none;
  }
  .lockup__name {
    font-weight: 600;
    font-size: 28px;
    letter-spacing: 1px;
    color: var(--grey);
    line-height: 1.1;
    white-space: nowrap;
  }
  .lockup__title {
    font-weight: 500;
    font-size: 17px;
    letter-spacing: 3px;
    color: var(--grey);
    margin-top: 6px;
    white-space: nowrap;
  }
  .card--front {
    display: flex;
    align-items: center;
    justify-content: center;
  }
  .card--front .services {
    font-weight: 600;
    font-size: 17px;
    color: var(--grey);
    margin-top: 12px;
  }
  .card--back .lockup {
    position: absolute;
    top: 70px;
    left: 50%;
    transform: translateX(-50%);
  }
  .details {
    position: absolute;
    left: 48px;
    right: 40px;
    bottom: 70px;
    display: flex;
    align-items: center;
  }
  .person { padding-right: 22px; white-space: nowrap; }
  .person__name {
    color: var(--red);
    font-weight: 700;
    font-size: 16px;
    margin-bottom: 8px;
  }
  .person__address {
    color: var(--light);
    font-size: 15px;
    line-height: 1.6;
  }
  .divider {
    width: 2px;
    height: 110px;
    background: var(--red);
    flex: none;
  }
  .contacts {
    list-style: none;
    padding-left: 22px;
    white-space: nowrap;
  }
  .contacts li {
    display: flex;
    align-items: center;
    gap: 12px;
    color: var(--light);
    font-size: 15px;
    line-height: 2;
  }
  .contacts svg { width: 15px; height: 15px; fill: var(--red); flex: none; }
</style>
</head>
<body>

  <section class="card card--front">
    <div class="lockup">
      <div class="lockup__square"></div>
      <div>
        <div class="lockup__name">DARIO WHITCOMBE, CPA, LLC</div>
        <div class="lockup__title">CERTIFIED PUBLIC ACCOUNTANT</div>
        <div class="services">Accounting, Tax &amp; Consulting Services</div>
      </div>
    </div>
  </section>

  <section class="card card--back">
    <div class="lockup">
      <div class="lockup__square"></div>
      <div>
        <div class="lockup__name">DARIO WHITCOMBE, CPA, LLC</div>
        <div class="lockup__title">CERTIFIED PUBLIC ACCOUNTANT</div>
      </div>
    </div>

    <div class="details">
      <div class="person">
        <div class="person__name">DARIO WHITCOMBE, PRINCIPAL</div>
        <div class="person__address">Harlow Plaza 1820 Lake<br>Crest Dr NW Suite 310</div>
      </div>
      <div class="divider"></div>
      <ul class="contacts">
        <li>
          <svg viewBox="0 0 16 16" aria-hidden="true"><path d="M3.2 1.5l2.3 2.6-1.2 1.6c.9 2 2.4 3.5 4.4 4.5l1.6-1.2 2.6 2.3-1.3 2.4C6.3 13.4 2.5 9.6 1 4.3z"/></svg>
          555-204-7731
        </li>
        <li>
          <svg viewBox="0 0 16 16" aria-hidden="true"><path d="M1 3h14v1.2L8 9 1 4.2z"/><path d="M1 5.8l7 4.7 7-4.7V13H1z"/></svg>
          info@whitcombecpallc.com
        </li>
        <li>
          <svg viewBox="0 0 16 16" aria-hidden="true"><path d="M8 1a7 7 0 1 0 0 14A7 7 0 0 0 8 1zm0 1.5c.8.8 1.4 2 1.7 3.5H6.3C6.6 4.5 7.2 3.3 8 2.5zM2.6 7h2.6a11 11 0 0 0 0 2H2.6a5.5 5.5 0 0 1 0-2zm3.7 3h3.4c-.3 1.5-.9 2.7-1.7 3.5-.8-.8-1.4-2-1.7-3.5zm4.5-1a11 11 0 0 0 0-2h2.6a5.5 5.5 0 0 1 0 2z"/></svg>
          www.whitcombecpallc.com
        </li>
      </ul>
    </div>
  </section>

</body>
</html>
```